Email Preference Page Design

We are looking for a 2 page design for our users to edit their email preferences and submit friend referrals. You can find the fuctionality, content and text here:

https://brightvanta.mailrelayhub.example/app/linkClick/7281/5fa9c1d3b07e442b/28374615/9bd4e01a7c3f2a65

* the shipping and billing address might be different so you need to show the billing if the "same as shipping" box is not checked. It can auto-hide like the page above shows if that fits your design.

* when the "unsubscribe from all email lists" box is selected, all the other checkbox options will hide as in the example page. We need you to show us what the site will look like with and without that checkbox selected.

We want to match these two pages to the general feel of these website pages:

www.brightvanta.com
and
free.brightvanta.com

The page should be very clean and tight. Project is for design only but must be able to be implemented in html showing button and checkbox states. Technically this must be two pages for our system - one for all the user info and one for individual email referrals (see example above).

Target Market(s)

video professionals

Industry/Entity Type

Shipping

Requirements
Must have
• our logo (see numerous versions attached)
well designed header
well designed sections
clean editable text
tight layout
html friendly
easy to understand
2 pages
Nice to have
• custom checkboxes and radio buttons

```html
<!DOCTYPE html>
<html lang="en">
<head>
<meta charset="utf-8">
<title>BrightVanta – Communication Preferences</title>
<link href="https://fonts.googleapis.com/css2?family=Exo+2:wght@500;600&family=Open+Sans:ital,wght@0,400;0,600;0,700;1,400&display=swap" rel="stylesheet">
<style>
  :root {
    --orange: #f58a33;
    --header: #2e3a46;
    --title: #33475b;
    --label: #555b61;
    --field-border: #d9dcde;
    --field-focus-bg: #f0f8fc;
    --field-focus-border: #a9c6d3;
    --white: #ffffff;
    --ink: #1e2429;
  }
  * { box-sizing: border-box; margin: 0; padding: 0; }
  html, body { width: 1200px; height: 2590px; overflow: hidden; }
  body {
    position: relative;
    background: var(--white);
    font-family: "Open Sans", Arial, sans-serif;
    color: var(--label);
  }

  /* Header */
  .site-header {
    position: absolute; left: 0; top: 0; width: 1200px; height: 211px;
    background: var(--header);
    display: flex; align-items: center; justify-content: center; gap: 26px;
  }
  .brand-dot { width: 78px; height: 78px; border-radius: 50%; background: var(--orange); }
  .brand-name {
    font-family: "Exo 2", Arial, sans-serif; font-weight: 500;
    font-size: 112px; line-height: 1; color: var(--white); letter-spacing: 1px;
    margin-top: -12px;
  }
  .required-tag {
    position: absolute; right: 0; top: 211px; height: 36px; width: 200px;
    background: var(--orange); color: var(--white);
    font-size: 16px; line-height: 36px; text-align: right; padding-right: 14px;
    clip-path: polygon(0 0, 100% 0, 100% 100%, 22px 100%);
  }

  .page-title {
    position: absolute; left: 0; top: 282px; width: 1200px; text-align: center;
    font-family: "Exo 2", Arial, sans-serif; font-weight: 600;
    font-size: 54px; color: var(--title); letter-spacing: 1px;
  }

  /* Section headings */
  .section-heading {
    position: absolute; height: 49px;
    font-family: "Exo 2", Arial, sans-serif; font-weight: 500;
    font-size: 29px; color: var(--orange);
    border-bottom: 3px solid var(--orange);
  }
  .section-heading::after {
    content: ""; position: absolute; left: 16px; bottom: -14px;
    border: 11px solid transparent; border-top-color: var(--orange); border-bottom: 0;
  }
  .contact-heading { left: 52px; top: 386px; width: 509px; }
  .shipping-heading { left: 639px; top: 386px; width: 509px; }

  /* Form fields */
  .field-list { position: absolute; display: grid; grid-auto-rows: 52px; row-gap: 8px; }
  .contact-fields { left: 38px; top: 471px; grid-template-columns: 164px 347px; }
  .shipping-fields { left: 630px; top: 575px; grid-template-columns: 173px 333px; }
  .field-label {
    font-size: 22px; color: var(--label); text-align: right; padding-right: 12px;
    align-self: center;
  }
  .field {
    height: 52px; border: 2px solid var(--field-border); background: var(--white);
    font-size: 21px; color: var(--label); padding: 0 15px; line-height: 48px;
    position: relative;
  }
  .field.is-focused { background: var(--field-focus-bg); border-color: var(--field-focus-border); }
  .field.select::after {
    content: ""; position: absolute; right: 40px; top: 6px; bottom: 6px;
    border-left: 2px solid var(--field-border);
  }
  .select-arrow { position: absolute; right: 10px; top: 18px; }
  .postal { display: flex; align-items: center; gap: 0; }
  .postal .field { width: 138px; }
  .postal .field.plus4 { width: 169px; }
  .plus { width: 40px; text-align: center; font-size: 20px; }
  .shipping-fields .postal .field { width: 140px; }
  .shipping-fields .postal .field.plus4 { width: 153px; }

  .same-address {
    position: absolute; left: 639px; top: 466px; width: 509px;
    display: flex; gap: 14px; font-size: 29px; line-height: 36px; color: var(--title);
  }
  .box {
    flex: none; width: 24px; height: 24px; border: 2px solid #c3c7cb; background: var(--white);
    margin-top: 6px;
  }

  /* Email preferences */
  .prefs {
    position: absolute; left: 0; top: 1262px; width: 1200px; height: 1328px;
    background: var(--orange); color: var(--white);
  }
  .prefs-badge {
    position: absolute; left: 555px; top: 1217px; width: 90px; height: 90px;
    border-radius: 50%; background: var(--orange);
  }
  .prefs-badge::after {
    content: ""; position: absolute; left: 27px; top: 27px; width: 36px; height: 36px;
    border-radius: 50%; background: var(--white);
  }
  .white-box {
    flex: none; width: 24px; height: 24px; background: var(--white); border: 2px solid #e9e9e9;
  }
  .subscribe { position: absolute; left: 52px; top: 124px; display: flex; gap: 16px; }
  .subscribe .white-box { margin-top: 8px; }
  .subscribe-title { font-size: 29px; font-weight: 700; line-height: 38px; }
  .subscribe-note { font-size: 27px; font-style: italic; line-height: 36px; opacity: .95; }
  .filter-note { position: absolute; left: 48px; top: 213px; font-size: 29px; font-weight: 700; }

  .topic-heading {
    position: absolute; width: 510px; height: 92px; padding-top: 6px;
    border-top: 3px solid var(--white); border-bottom: 3px solid var(--white);
    font-family: "Exo 2", Arial, sans-serif; font-weight: 500; font-size: 30px; line-height: 31px;
  }
  .topic-heading::after {
    content: ""; position: absolute; left: 20px; bottom: -14px;
    border: 11px solid transparent; border-top-color: var(--white); border-bottom: 0;
  }
  .topics-left-heading { left: 60px; top: 280px; }
  .topics-right-heading { left: 634px; top: 280px; }

  .topic-list { position: absolute; list-style: none; }
  .topic-list li {
    display: flex; align-items: center; gap: 17px; height: 53.5px;
    font-size: 22px; color: var(--white);
  }
  .topic-list .white-box { width: 23px; height: 23px; }
  .topics-left { left: 55px; top: 401px; }
  .topics-right { left: 639px; top: 401px; }

  .unsubscribe {
    position: absolute; left: 639px; top: 843px; width: 508px; height: 64px;
    background: var(--white); color: var(--ink);
    display: flex; align-items: center; gap: 16px; padding-left: 16px;
    font-size: 29px;
  }
  .unsubscribe .box { margin-top: 0; }

  .submit-button {
    position: absolute; left: 54px; top: 1156px; width: 360px; height: 79px;
    background: var(--white); border: 0; color: var(--ink);
    font-family: "Open Sans", Arial, sans-serif; font-weight: 600; font-size: 38px;
  }
</style>
</head>
<body>
  <header class="site-header">
    <span class="brand-dot" aria-hidden="true"></span>
    <span class="brand-name">brightvanta</span>
  </header>
  <div class="required-tag">Required Fields*</div>

  <h1 class="page-title">COMMUNICATION PREFERENCES</h1>

  <h2 class="section-heading contact-heading">Contact Info</h2>
  <div class="field-list contact-fields">
    <span class="field-label">First Name*</span><div class="field is-focused"></div>
    <span class="field-label">Last Name*</span><div class="field"></div>
    <span class="field-label">Email *</span><div class="field"></div>
    <span class="field-label">Phone</span><div class="field"></div>
    <span class="field-label">Address 1</span><div class="field"></div>
    <span class="field-label">Address 2</span><div class="field"></div>
    <span class="field-label">Address 3</span><div class="field"></div>
    <span class="field-label">City</span>
    <div class="field select"><svg class="select-arrow" width="18" height="14" viewBox="0 0 18 14"><path d="M2 2h14L9 12z" fill="#b8bcc0"/></svg></div>
    <span class="field-label">Select Country</span><div class="field"></div>
    <span class="field-label">State</span><div class="field"></div>
    <span class="field-label">Postal Code + 4</span>
    <div class="postal"><div class="field">11111</div><span class="plus">+</span><div class="field plus4">1111</div></div>
  </div>

  <h2 class="section-heading shipping-heading">Shipping Address</h2>
  <div class="same-address"><span class="box"></span><span>Billing address is same as shipping address</span></div>
  <div class="field-list shipping-fields">
    <span class="field-label">Street Address 1</span><div class="field"></div>
    <span class="field-label">Street Address 2</span><div class="field"></div>
    <span class="field-label">Street Address 3</span><div class="field"></div>
    <span class="field-label">City</span>
    <div class="field select"><svg class="select-arrow" width="18" height="14" viewBox="0 0 18 14"><path d="M2 2h14L9 12z" fill="#b8bcc0"/></svg></div>
    <span class="field-label">Select Country</span><div class="field"></div>
    <span class="field-label">State</span><div class="field"></div>
    <span class="field-label">Postal Code + 4</span>
    <div class="postal"><div class="field">44444</div><span class="plus">+</span><div class="field plus4">2222</div></div>
  </div>

  <section class="prefs">
    <div class="subscribe">
      <span class="white-box"></span>
      <div>
        <p class="subscribe-title">Subscribe me to your general email list</p>
        <p class="subscribe-note">This monthly email includes free video loops and VIP sale notices</p>
      </div>
    </div>
    <p class="filter-note">Help us filter our emails so we only sending relevant information to you</p>

    <h3 class="topic-heading topics-left-heading">Send me emails about these product types:</h3>
    <h3 class="topic-heading topics-right-heading">Send me emails about these product types:</h3>

    <ul class="topic-list topics-left">
      <li><span class="white-box"></span>Low energy motion loops</li>
      <li><span class="white-box"></span>High energy motion loops</li>
      <li><span class="white-box"></span>Timelapse footage</li>
      <li><span class="white-box"></span>Low energy motion loops</li>
      <li><span class="white-box"></span>High energy motion loops</li>
      <li><span class="white-box"></span>Timelapse footage</li>
      <li><span class="white-box"></span>Worship or wedding motion loops</li>
      <li><span class="white-box"></span>Pre-mixed DVDs and BluRay</li>
      <li><span class="white-box"></span>Entertainment lasers for concerts and clubs</li>
      <li><span class="white-box"></span>Entertainment lasers for text &amp; logo display</li>
      <li><span class="white-box"></span>Custom logo animation services</li>
      <li><span class="white-box"></span>Video software for creating video animations</li>
      <li><span class="white-box"></span>Video software for live performance (Vjing)</li>
    </ul>

    <ul class="topic-list topics-right">
      <li><span class="white-box"></span>Vjing (live performance video)</li>
      <li><span class="white-box"></span>DJing (live performance audio+video)</li>
      <li><span class="white-box"></span>Performing in a band</li>
      <li><span class="white-box"></span>Video editing</li>
      <li><span class="white-box"></span>Corporate presentations</li>
      <li><span class="white-box"></span>Worship video services</li>
      <li><span class="white-box"></span>Lasers for entertainment &amp; branding</li>
      <li><span class="white-box"></span>Special offers from BrightVanta partners</li>
    </ul>

    <div class="unsubscribe"><span class="box"></span>Unsubscribe from all email lists</div>

    <button class="submit-button" type="button">Submit Now</button>
  </section>
  <div class="prefs-badge" aria-hidden="true"></div>
</body>
</html>
```